VFX Company Business Card Design Project

The Kestrel Works is a decentralized Visual Effects Studio servicing the television and feature film industries.
Project Brief:
Take our logo that was previously designed on Pencil Harbor and make a double sided business card.
Requirements:
- Card MUST be double sided.
- Front of card MUST have the yellow part of our logo against the dark grey background.
- Back of card is completely up to the designer.
- Back of card must include the complete company logo.
Please follow these File Preparation guidelines:
http://printnook.ca/infopage?file=filetype_en&s=PrintNook_new&lang=en
Business

```html
<!DOCTYPE html>
<html lang="en">
<head>
<meta charset="utf-8">
<title>The Kestrel Works – Business Cards</title>
<link href="https://fonts.googleapis.com/css2?family=Jost:wght@400;600&family=PT+Serif:wght@400;700&display=swap" rel="stylesheet">
<style>
  :root{
    --backdrop:#86461f;
    --card:#262626;
    --yellow:#f9c41e;
    --light:#eef2e6;
    --slate:#5f6b70;
    --band-line:#d9ddd2;
  }
  *{margin:0;padding:0;box-sizing:border-box}
  html,body{width:1200px;height:733px;overflow:hidden;background:var(--backdrop)}
  .sheet{position:relative;width:1200px;height:733px;background:var(--backdrop)}
  .card{position:absolute;width:524px;height:300px;background:var(--card);border-radius:28px;overflow:hidden}
  .card--front{left:70px;top:43px}
  .card--details{left:630px;top:48px;width:525px}
  .card--lockup{left:66px;top:385px}
  .card--wordmark{left:624px;top:388px}

  .brand{font-family:"Jost",sans-serif;font-weight:600;letter-spacing:-0.5px;white-space:nowrap;line-height:1}
  .tagline{font-family:"Jost",sans-serif;font-weight:400;color:var(--light);letter-spacing:6px;text-transform:uppercase;white-space:nowrap;line-height:1}
  .url{position:absolute;left:0;right:0;bottom:22px;text-align:center;font-family:"Jost",sans-serif;font-size:18px;letter-spacing:3px;color:var(--light)}

  /* front */
  .front-mark{position:absolute;inset:0;display:flex;align-items:center;justify-content:center;gap:18px}
  .front-mark .dot{width:34px;height:34px;border-radius:50%;background:var(--yellow)}
  .front-mark .brand{font-size:48px;color:var(--yellow)}

  /* details side */
  .details-head{position:absolute;top:38px;left:0;right:0;text-align:center}
  .details-head .brand{font-size:44px;color:var(--light)}
  .details-head .tagline{font-size:19px;margin-top:10px;color:var(--light)}
  .name-band{position:absolute;left:0;right:0;top:155px;height:42px;background:var(--light);
    border-top:3px double var(--band-line);display:flex;align-items:center;justify-content:center;
    font-family:"PT Serif",serif;color:#1e1e1e}
  .name-band::before,.name-band::after{content:"";position:absolute;left:0;right:0;height:1px;background:var(--band-line)}
  .name-band::before{top:-8px}
  .name-band::after{bottom:-5px}
  .name-band strong{font-size:20px;font-weight:700}
  .name-band span{font-size:15px;margin-left:6px}
  .contact{position:absolute;top:210px;left:0;right:0;font-family:"PT Serif",serif;font-size:14.5px;color:var(--light)}
  .address{position:absolute;right:287px;top:18px;text-align:right;line-height:20px}
  .divider{position:absolute;left:252px;top:10px;width:2px;height:62px;background:var(--light);opacity:.8}
  .lines{position:absolute;left:268px;top:0;list-style:none;line-height:19.3px}
  .lines li{display:flex;align-items:center;gap:5px}
  .lines svg{width:11px;height:11px;fill:var(--light)}

  /* lockup back */
  .lockup{position:absolute;left:36px;right:20px;top:105px;display:flex;align-items:center;gap:22px}
  .lockup .dot{width:60px;height:60px;border-radius:50%;background:var(--yellow);flex:none}
  .lockup .brand{font-size:36px;color:var(--light)}
  .lockup .tagline{font-size:15px;margin-top:8px;letter-spacing:5px}

  /* wordmark back */
  .wordmark{position:absolute;top:100px;left:0;right:0;text-align:center}
  .wordmark .brand{font-size:48px;color:var(--light)}
  .wordmark .tagline{font-size:21px;margin-top:12px}
</style>
</head>
<body>
<main class="sheet">

  <section class="card card--front" aria-label="Card front">
    <div class="front-mark">
      <span class="dot"></span>
      <span class="brand">The Kestrel Works</span>
    </div>
  </section>

  <section class="card card--details" aria-label="Card back with contact details">
    <header class="details-head">
      <div class="brand">The Kestrel Works</div>
      <div class="tagline">Virtual Studio</div>
    </header>
    <div class="name-band"><strong>Your Name,</strong><span>Title</span></div>
    <div class="contact">
      <address class="address" style="font-style:normal">00, Complex name<br>City, State 0042</address>
      <span class="divider"></span>
      <ul class="lines">
        <li><svg viewBox="0 0 12 12"><path d="M2.5 1l2 2.2-1 1.3c.8 1.6 2 2.8 3.6 3.6l1.3-1L11 9.5 9.6 11C5 10.6 1.4 7 1 2.4z"/></svg>0987 654321</li>
        <li><svg viewBox="0 0 12 12"><path d="M3 2h6l1.5 4H11v4H9V9H3v1H1V6h.5z M3.3 5h5.4l-.8-2H4.1z"/></svg>0987 654321</li>
        <li><svg viewBox="0 0 12 12"><path d="M1 3h10v7H1z M1.5 3.5 6 7l4.5-3.5" stroke="#262626" stroke-width="1"/></svg>info@kestrelworks.com</li>
        <li><svg viewBox="0 0 12 12"><circle cx="6" cy="6" r="5"/><path d="M1 6h10M6 1v10M3 2.5c2 1 4 1 6 0M3 9.5c2-1 4-1 6 0" stroke="#262626" stroke-width=".8" fill="none"/></svg>www.kestrelworks.com</li>
      </ul>
    </div>
  </section>

  <section class="card card--lockup" aria-label="Card back with logo lockup">
    <div class="lockup">
      <span class="dot"></span>
      <div>
        <div class="brand">The Kestrel Works</div>
        <div class="tagline">Virtual Studio</div>
      </div>
    </div>
    <p class="url">www.kestrelworks.com</p>
  </section>

  <section class="card card--wordmark" aria-label="Card back with wordmark">
    <div class="wordmark">
      <div class="brand">The Kestrel Works</div>
      <div class="tagline">Virtual Studio</div>
    </div>
    <p class="url">www.kestrelworks.com</p>
  </section>

</main>
</body>
</html>
```